Sunset Harbor Living Web Page

We need a web page design that has two intro pages - first being a 'home page', then a link to the second page that has the 'content tabs' and a 'call to action' (see below).

The business helps people that wish to retire to S.E.Asia (Thailand, Malaysia, Indonesia,The Philippines etc) - to enjoy the lifestyle and the remaining years of their lives. What attracts S.E.Asia to many people is the lower cost, the atmoshpere and beauty of the tropics and the vibrancy of the various countries.

People that are wishing to make the most of their retirement and are adventurous at a great bargain compared to the cost of their own countries will be interested.

We help them achieve this - visa, financials (tax, gov't payments etc), introduce them to the right people for property, clubs, retirement facilities, insurance and so forth.

Therefore we are providing an extremely wide ranging service and this site will provide broad but general information only - with a call to action to come and see us for more specific information and how we can help them specifically.

This site will be predominantly for travel and lifestyle, it will be linked with another financial services (financial planning) site later down the track.

The colour scheme is dark green and blue - as per the attached logo design. Photos and background just think lifestyle and S.E.Asia - beaches/mountains/water/recreational activities for retirees.

Target market is mostly those coming up to retirement to those that are already retired. But we also expect to have some interest with younger people that would like to find out more and plan for the future. So a broad age group but I would say mostly 40-70 yrs old.

On the first (Home) page we would like our company name 'Sunset Harbor Living', our logo (which will be on all pages) and a statement such as: “Imagine a retirement where your dreams are brought to life, and you have never felt more alive. Let us show you how”. Then a link to the second page.

We would like an uncluttered site. On the second (contents) page the tabs would be:

- Visa
- Property
- Financials
- Travel
- Insurance & Healthcare
- Medical Tourism
- Cost of living
- Weekly Blogs and articles
- Sunset Harbor Living story

We would also like a call to action on the second page - asking them to leave their contact details if they wish to learn more or sign up to our weekly newsletter/blog.

We are open to suggestions and your imaginations.

Thank you
Malcolm

Font styles to use
Serif
Script

Colors
0255a3
3377b5
00a990
9bcb3c
abd036
33b8a4
85abd2
cadf82
86cfc6

Requirements
Must have
• I have been asked by the web designer to receive a 'Web Font' so that we can 'get off of Zentrofy'. Hope that makes sense.

```html
<!DOCTYPE html>
<html lang="en">
<head>
<meta charset="utf-8">
<title>Sunset Harbor Living – Home</title>
<link rel="stylesheet" href="https://fonts.googleapis.com/css2?family=Roboto+Condensed:wght@400;700&display=swap">
<style>
  :root {
    --brand-blue: #0255a3;
    --sky-blue: #0aaee6;
    --nav-blue-dark: #0378c4;
    --brand-green: #00a990;
    --lime: #9bcb3c;
    --lime-ring: #cfe59a;
    --text-grey: #6b6b6b;
    --white: #ffffff;
    --footer-bg: #111111;
    --footer-text: #9a9a9a;
  }
  * { margin: 0; padding: 0; box-sizing: border-box; }
  html, body { width: 1200px; height: 686px; overflow: hidden; background: var(--white); }
  body { font-family: "Roboto Condensed", "Arial Narrow", sans-serif; position: relative; }

  .top-stripe { height: 4px; background: linear-gradient(90deg, var(--brand-green), var(--sky-blue)); }

  .site-header { height: 97px; position: relative; }
  .brand { position: absolute; left: 98px; top: 30px; display: flex; align-items: center; gap: 8px; }
  .brand-mark { width: 36px; height: 36px; border-radius: 50%; background: var(--brand-green); }
  .brand-name { font-size: 19px; font-weight: 700; color: var(--brand-blue); line-height: 1; }

  .contact-item { position: absolute; top: 25px; display: flex; align-items: center; }
  .contact-phone { left: 675px; }
  .contact-mail { left: 890px; }
  .contact-icon { width: 46px; height: 46px; border-radius: 50%; background: var(--lime); border: 3px solid var(--lime-ring); display: flex; align-items: center; justify-content: center; }
  .contact-text { margin-left: 22px; color: var(--text-grey); font-size: 14px; line-height: 21px; }

  .main-nav { height: 58px; background: linear-gradient(180deg, var(--sky-blue), var(--nav-blue-dark)); border-bottom: 2px solid var(--brand-green); position: relative; }
  .main-nav ul { list-style: none; display: flex; gap: 19px; position: absolute; left: 99px; top: 0; height: 56px; align-items: center; }
  .main-nav a { color: var(--white); text-decoration: none; font-size: 14px; }
  .main-nav .is-current { position: relative; }
  .main-nav .is-current::after { content: ""; position: absolute; left: 50%; margin-left: -5px; bottom: -21px; border: 5px solid transparent; border-bottom-color: var(--brand-green); }

  .hero { height: 464px; position: relative; overflow: hidden; }
  .hero-photo { position: absolute; inset: 0;
    background:
      linear-gradient(180deg, rgba(0,0,0,0.25), rgba(0,0,0,0.35)),
      radial-gradient(ellipse at 70% 25%, #c9a26a 0%, #8d7a63 35%, transparent 70%),
      linear-gradient(180deg, #7d7a72 0%, #6a6256 40%, #3e4a3a 62%, #4d4a45 78%, #2f2d2b 100%); }
  .hero-heading { position: absolute; left: 0; right: 0; top: 130px; text-align: center; color: var(--white); font-weight: 700; font-size: 34px; line-height: 52px; text-transform: uppercase; letter-spacing: 0.2px; }
  .hero-cta { position: absolute; left: 454px; top: 275px; width: 273px; height: 48px; border: 2px solid var(--white); border-radius: 24px; color: var(--white); font-size: 23px; text-decoration: none; display: flex; align-items: center; justify-content: center; }
  .slider-arrow { position: absolute; top: 212px; width: 40px; height: 40px; }
  .slider-prev { left: 38px; }
  .slider-next { left: 1127px; }

  .site-footer { position: absolute; left: 0; top: 623px; width: 1200px; height: 63px; background: var(--footer-bg); color: var(--footer-text); font-size: 12px; }
  .legal { position: absolute; left: 52px; top: 24px; }
  .legal span.sep { margin: 0 8px; }
  .social { position: absolute; left: 815px; top: 25px; display: flex; align-items: center; gap: 15px; }
  .social-dot { width: 10px; height: 10px; border-radius: 50%; background: #7a7a7a; }
</style>
</head>
<body>
  <div class="top-stripe"></div>

  <header class="site-header">
    <div class="brand">
      <span class="brand-mark"></span>
      <span class="brand-name">Sunset Harbor Living</span>
    </div>
    <div class="contact-item contact-phone">
      <span class="contact-icon">
        <svg width="18" height="18" viewBox="0 0 24 24"><path fill="#fff" d="M6.6 10.8a15.1 15.1 0 0 0 6.6 6.6l2.2-2.2c.3-.3.7-.4 1-.2 1.1.4 2.3.6 3.6.6.6 0 1 .4 1 1V20c0 .6-.4 1-1 1A17 17 0 0 1 3 4c0-.6.4-1 1-1h3.5c.6 0 1 .4 1 1 0 1.3.2 2.5.6 3.6.1.3 0 .7-.2 1z"/></svg>
      </span>
      <div class="contact-text">CALL US ON :<br>(088) - 5550142870</div>
    </div>
    <div class="contact-item contact-mail">
      <span class="contact-icon">
        <svg width="20" height="16" viewBox="0 0 20 16"><rect x="1" y="1" width="18" height="14" rx="2" fill="none" stroke="#fff" stroke-width="2"/><path d="M1.5 2.5 10 9l8.5-6.5" fill="none" stroke="#fff" stroke-width="2"/></svg>
      </span>
      <div class="contact-text">MAIL US ON :<br>Info@sunsetharborliving.com</div>
    </div>
  </header>

  <nav class="main-nav">
    <ul>
      <li><a class="is-current" href="#">Home</a></li>
      <li><a href="#">Visa</a></li>
      <li><a href="#">Property</a></li>
      <li><a href="#">Financials</a></li>
      <li><a href="#">Travel</a></li>
      <li><a href="#">Insurance &amp; Healthcare</a></li>
      <li><a href="#">Medical Tourism</a></li>
      <li><a href="#">Cost of living</a></li>
      <li><a href="#">Weekly Blogs and articles</a></li>
      <li><a href="#">Sunset Harbor Living story</a></li>
      <li><a href="#">Contact us</a></li>
    </ul>
  </nav>

  <section class="hero">
    <div class="hero-photo" role="img" aria-label="Lakeside temple with tiered roofs, mountains and a golden sunset sky over calm water"></div>
    <h1 class="hero-heading">Imagine a retirement where your dreams are<br>brought to life, and you have never felt more alive</h1>
    <a class="hero-cta" href="#">Let us show you how</a>
    <svg class="slider-arrow slider-prev" viewBox="0 0 40 40" aria-hidden="true"><circle cx="20" cy="20" r="18.5" fill="none" stroke="rgba(255,255,255,0.7)" stroke-width="2"/><path d="M25 11 13 20l12 9-3-9z" fill="rgba(255,255,255,0.7)"/></svg>
    <svg class="slider-arrow slider-next" viewBox="0 0 40 40" aria-hidden="true"><circle cx="20" cy="20" r="18.5" fill="none" stroke="rgba(255,255,255,0.7)" stroke-width="2"/><path d="M15 11 27 20l-12 9 3-9z" fill="rgba(255,255,255,0.7)"/></svg>
  </section>

  <footer class="site-footer">
    <div class="legal">© 2016 Company Name . all rights reserved<span class="sep">/</span>Terms and Conditions<span class="sep">/</span>Privacy policy</div>
    <div class="social">
      <span>Connect with our social network :</span>
      <span class="social-dot" aria-label="Social network 1"></span>
      <span class="social-dot" aria-label="Social network 2"></span>
      <span class="social-dot" aria-label="Social network 3"></span>
      <span class="social-dot" aria-label="Social network 4"></span>
    </div>
  </footer>
</body>
</html>
```